Colin Vardek Business card

Hey there, I’m hoping to have a business card designed. I’m in Real estate and just switched to a new Brokerage called: The Harbourline Property Group

The back could just be the company name maybe or whatever looks good!

I’ve attached some logos of our company and some cards my buddy had done up.

On the card:
Colin Vardek
colinvardek@mailora.com
587-412-9065
colinvardek.ca

Target Market(s)

Home buyers and sellers

Industry/Entity Type

Real Estate

Contact Information for Business Card

just looking for a cool and modern design with my picture on it. I like the idea of Black and red being used.

Requirements
Must have
• all the details provided. I'm open to anything. Just want a professional looking card.

```html
<!DOCTYPE html>
<html lang="en">
<head>
<meta charset="utf-8">
<title>Colin Vardek — Business Card</title>
<link rel="stylesheet" href="https://fonts.googleapis.com/css2?family=Lato:wght@400;700;900&display=swap">
<style>
  :root {
    --stage: #121212;
    --card: #141414;
    --card-light: #1f1f1f;
    --red: #d81f3a;
    --white: #f4f4f4;
    --grey: #8a8a8a;
    --photo-a: #2b2f36;
    --photo-b: #0f1012;
  }
  * { margin: 0; padding: 0; box-sizing: border-box; }
  html, body { width: 1200px; height: 977px; overflow: hidden; background: var(--stage); }
  body { font-family: "Lato", sans-serif; color: var(--white); position: relative; }

  .card {
    position: absolute;
    left: 240px;
    width: 720px;
    height: 412px;
    border-radius: 22px;
    background: radial-gradient(ellipse at 45% 35%, var(--card-light), var(--card) 70%);
    border: 3px solid var(--red);
    overflow: hidden;
  }
  .card--back { top: 60px; }
  .card--front { top: 505px; }

  /* Back */
  .back-brand {
    position: absolute; inset: 0;
    display: flex; flex-direction: column; align-items: center; justify-content: center;
    gap: 14px;
  }
  .back-brand__name {
    font-weight: 900; font-size: 58px; letter-spacing: 2px; text-transform: uppercase;
    color: #6f6f6f;
  }
  .back-brand__group {
    display: flex; align-items: center; gap: 12px;
    font-size: 15px; letter-spacing: 4px; text-transform: uppercase; color: #5c5c5c;
  }
  .back-brand__group::before, .back-brand__group::after {
    content: ""; width: 60px; height: 1px; background: #4a4a4a;
  }

  /* Front */
  .front-brand { position: absolute; left: 48px; top: 58px; }
  .front-brand__name {
    display: flex; align-items: center; gap: 12px;
    font-weight: 900; font-size: 38px; text-transform: uppercase; color: var(--white);
  }
  .front-brand__mark { width: 16px; height: 16px; background: var(--red); }
  .front-brand__group {
    margin-top: 8px; padding-top: 6px; border-top: 1px solid var(--grey);
    font-size: 11px; letter-spacing: 3px; text-transform: uppercase; color: var(--white);
    display: inline-block;
  }

  .agent { position: absolute; left: 48px; top: 200px; }
  .agent__name { font-weight: 900; font-size: 30px; text-transform: uppercase; color: var(--red); line-height: 1; }
  .agent__role { margin-top: 6px; font-size: 17px; text-transform: uppercase; color: var(--white); }

  .contact { position: absolute; left: 48px; top: 290px; list-style: none; }
  .contact__item { display: flex; align-items: center; gap: 14px; font-size: 19px; margin-bottom: 10px; }
  .contact__icon { width: 16px; height: 16px; flex: none; }

  .agent-photo {
    position: absolute; right: 0; bottom: 0; width: 300px; height: 350px;
    background: radial-gradient(ellipse at 50% 30%, var(--photo-a), var(--photo-b) 75%);
  }
  .brokerage {
    position: absolute; right: 26px; top: 26px; width: 150px; text-align: right;
    font-weight: 900; font-size: 15px; line-height: 1.2; text-transform: uppercase; color: var(--white);
  }
</style>
</head>
<body>

<section class="card card--back" aria-label="Card back">
  <div class="back-brand">
    <div class="back-brand__name">Colin Vardek</div>
    <div class="back-brand__group">The Harbourline Property Group</div>
  </div>
</section>

<section class="card card--front" aria-label="Card front">
  <div class="front-brand">
    <div class="front-brand__name"><span class="front-brand__mark"></span>Colin Vardek</div>
    <div class="front-brand__group">The Harbourline Property Group</div>
  </div>

  <div class="agent">
    <div class="agent__name">Colin Vardek</div>
    <div class="agent__role">Realtor</div>
  </div>

  <ul class="contact">
    <li class="contact__item">
      <svg class="contact__icon" viewBox="0 0 16 16"><path fill="#d81f3a" d="M3.5 1.5l2.5 0 1 3.5-1.8 1.2a9 9 0 004.6 4.6L11 9l3.5 1v2.5c0 1-1 2-2 2A11 11 0 011.5 3.5c0-1 1-2 2-2z"/></svg>
      587-412-9065
    </li>
    <li class="contact__item">
      <svg class="contact__icon" viewBox="0 0 16 16"><rect x="1" y="3" width="14" height="10" fill="#d81f3a"/><path d="M1.5 3.5L8 9l6.5-5.5" stroke="#141414" stroke-width="1.4" fill="none"/></svg>
      colinvardek@mailora.com
    </li>
    <li class="contact__item">
      <svg class="contact__icon" viewBox="0 0 16 16"><circle cx="8" cy="8" r="7" fill="#d81f3a"/><path d="M1 8h14M8 1c-3 3.5-3 10.5 0 14M8 1c3 3.5 3 10.5 0 14" stroke="#141414" stroke-width="1.1" fill="none"/></svg>
      colinvardek.ca
    </li>
  </ul>

  <div class="agent-photo" role="img" aria-label="Portrait photo of Colin Vardek in a dark suit and white shirt"></div>

  <div class="brokerage">The Harbourline Property Group</div>
</section>

</body>
</html>
```